Modern looking signage for dental office.

Exterior signage for passing cars
Updates
Need extra days to review
Target Market(s)
Cars passing by
Font styles to use
Sans Serif
Colors
3276b5
Requirements
Must have
- Logo
- OPEN ON SUTURDAY AND SUNDAY
- NIGHT CLINIC AVAILABLE
- PLEASE USE THE FONT TYPE IN FILE 4 UPLOADED BELOW.
- (847) 302-7469
- Modern looking

```html
<!DOCTYPE html>
<html lang="en">
<head>
<meta charset="UTF-8">
<title>Nova Dental – Exterior Sign</title>
<link rel="stylesheet" href="https://fonts.googleapis.com/css2?family=Josefin+Sans:wght@300&family=Montserrat:wght@800&family=Open+Sans:wght@600&display=swap">
<style>
  :root {
    --backdrop: #a4a4a4;
    --sign-white: #ffffff;
    --header-fade: #e9e9e9;
    --ink: #000000;
    --logo-ink: #3b3b3b;
    --brand-blue: #3276b5;
    --footer-grey: #dfdfdf;
    --divider: #9a9a9a;
    --icon-grey: #7a7a7a;
  }
  * { margin: 0; padding: 0; box-sizing: border-box; }
  html, body { width: 1200px; height: 1000px; overflow: hidden; }
  body { background: var(--backdrop); position: relative; }

  .sign {
    position: absolute; left: 192px; top: 92px;
    width: 818px; height: 815px;
    background: var(--sign-white);
    overflow: hidden;
  }
  .sign__header {
    position: absolute; left: 0; top: 0; width: 100%; height: 220px;
    background: linear-gradient(to bottom, var(--sign-white) 80%, var(--header-fade) 100%);
  }
  .brand-mark {
    position: absolute; left: 76px; top: 41px;
    width: 144px; height: 144px; border-radius: 50%;
    border: 2px solid var(--logo-ink);
  }
  .brand-name {
    position: absolute; left: 234px; top: 80px;
    font-family: "Josefin Sans", sans-serif; font-weight: 300;
    font-size: 72px; line-height: 1; letter-spacing: 0;
    color: var(--logo-ink); white-space: nowrap;
  }
  .brand-tagline {
    position: absolute; left: 0; width: 100%; top: 161px; text-align: center;
    padding-left: 140px;
    font-family: "Open Sans", sans-serif; font-weight: 600;
    font-size: 26px; color: var(--logo-ink); white-space: nowrap;
  }

  .rule { position: absolute; left: 0; width: 100%; background: var(--ink); }
  .rule--top { top: 220px; height: 10px; }
  .rule--bottom { top: 680px; height: 10px; }

  .sign__panel {
    position: absolute; left: 0; top: 238px; width: 100%; height: 432px;
    background: var(--ink); color: var(--sign-white);
    font-family: "Montserrat", sans-serif; font-weight: 800;
  }
  .line { position: absolute; white-space: nowrap; line-height: 1; }
  .line--open { left: 170px; top: 34px; font-size: 110px; }
  .line--days { left: 0; width: 100%; text-align: center; top: 144px; font-size: 54px; }
  .line--night { left: 112px; top: 260px; font-size: 90px; }
  .line--available { left: 0; width: 100%; text-align: center; top: 355px; font-size: 74px; }
  .divider {
    position: absolute; left: 174px; top: 232px; width: 468px; height: 2px;
    background: var(--divider);
  }
  .tooth-icon {
    position: absolute; border-radius: 40% 40% 30% 30%;
    background: linear-gradient(to bottom, #d8d8d8, #9a9a9a);
  }
  .tooth-icon--open { left: 76px; top: 40px; width: 72px; height: 84px; }
  .tooth-icon--night { left: 38px; top: 262px; width: 58px; height: 70px; }

  .sign__footer {
    position: absolute; left: 0; top: 690px; width: 100%; height: 125px;
    background: var(--footer-grey);
  }
  .phone-icon { position: absolute; left: 103px; top: 28px; width: 68px; height: 68px; }
  .phone-number {
    position: absolute; left: 192px; top: 22px;
    font-family: "Montserrat", sans-serif; font-weight: 800;
    font-size: 72px; line-height: 1.1; color: var(--ink); white-space: nowrap;
  }
</style>
</head>
<body>
  <section class="sign">
    <header class="sign__header">
      <div class="brand-mark"></div>
      <div class="brand-name">NOVA DENTAL</div>
      <div class="brand-tagline">MODERN GENERAL DENTISTRY</div>
    </header>

    <div class="rule rule--top"></div>

    <main class="sign__panel">
      <div class="tooth-icon tooth-icon--open" role="img" aria-label="Outlined tooth icon"></div>
      <div class="line line--open">OPEN ON</div>
      <div class="line line--days">SATURDAY AND SUNDAY</div>
      <div class="divider"></div>
      <div class="tooth-icon tooth-icon--night" role="img" aria-label="Outlined tooth icon"></div>
      <div class="line line--night">NIGHT CLINIC</div>
      <div class="line line--available">AVAILABLE</div>
    </main>

    <div class="rule rule--bottom"></div>

    <footer class="sign__footer">
      <svg class="phone-icon" viewBox="0 0 68 68" aria-hidden="true">
        <circle cx="34" cy="34" r="31" fill="none" stroke="var(--icon-grey)" stroke-width="5"/>
        <circle cx="34" cy="34" r="25" fill="var(--icon-grey)"/>
        <path d="M25 20c2-1 4 0 5 2l2 4c1 2 0 3-1 4l-2 1c1 4 4 7 8 9l1-2c1-1 2-2 4-1l4 2c2 1 3 3 2 5l-1 2c-1 2-4 3-7 2-9-3-16-10-19-19-1-3 0-6 2-7z" fill="var(--footer-grey)"/>
        <path d="M38 22a9 9 0 0 1 8 8M38 16a15 15 0 0 1 14 14" fill="none" stroke="var(--footer-grey)" stroke-width="2.5" stroke-linecap="round"/>
      </svg>
      <div class="phone-number">(847) 302-7469</div>
    </footer>
  </section>
</body>
</html>
```